Exciting & Elegant Stationary Pack

Stationary consists of
1. Letter head / Envelope
2. Business Card
3. Invoice
4. 40x40mm sticker

Attached files;

1. Logo (Other formats available on request)
2. MS word Doc - For information and description of design
3. Website image (This will be our new website so use the colours so everything ties together)
4. Sample of stationary pack we like, but feel free to be creative

Target Market(s)

Home improvement

Industry/Entity Type

Construction

Font styles to use
Other font styles liked:
• Leave up to designer - We like font used on (website attached image)

Requirements
Must have
• Please look at uploaded file of sample website and use colours
Nice to have
• Any type of business card design - eg. metal, die cut, embossed, etc...

```html
<!DOCTYPE html>
<html lang="en">
<head>
<meta charset="utf-8">
<title>Setwell Tiling – Business Card</title>
<link rel="stylesheet" href="https://fonts.googleapis.com/css2?family=Open+Sans:wght@400;700&display=swap">
<style>
  :root {
    --page-bg: #e9e7e4;
    --navy-deep: #0f1c2e;
    --navy: #1d3350;
    --navy-soft: #2b4563;
    --orange: #e0662a;
    --orange-deep: #c9521c;
    --frost-light: #f4f4f3;
    --frost-mid: #d9dbdc;
    --text-light: #e8ecf1;
  }
  * { margin: 0; padding: 0; box-sizing: border-box; }
  html, body {
    width: 1200px;
    height: 969px;
    overflow: hidden;
    background: var(--page-bg);
    font-family: "Open Sans", Arial, sans-serif;
  }
  .card {
    position: absolute;
    left: 75px;
    top: 186px;
    width: 1050px;
    height: 596px;
    overflow: hidden;
    box-shadow: 0 10px 30px rgba(0,0,0,0.18);
  }
  .card-art {
    position: absolute;
    inset: 0;
  }
  .contact-block {
    position: absolute;
    left: 43px;
    top: 166px;
    color: var(--text-light);
  }
  .person-name {
    color: var(--orange);
    font-weight: 700;
    font-size: 36px;
    line-height: 1.2;
  }
  .person-role {
    font-size: 28px;
    line-height: 1.3;
  }
  .licence {
    font-size: 27px;
    margin-top: 20px;
  }
  .contact-list {
    list-style: none;
    margin-top: 24px;
  }
  .contact-list li {
    display: flex;
    align-items: center;
    font-size: 28px;
    line-height: 40px;
  }
  .contact-icon {
    width: 24px;
    height: 24px;
    margin-right: 14px;
    flex: none;
  }
  .brand-name {
    position: absolute;
    left: 560px;
    top: 230px;
    width: 340px;
    text-align: center;
    font-weight: 700;
    font-size: 60px;
    line-height: 1.1;
    color: var(--navy);
  }
</style>
</head>
<body>
  <div class="card">
    <svg class="card-art" viewBox="0 0 1050 596" width="1050" height="596" aria-hidden="true">
      <defs>
        <linearGradient id="navyField" x1="0" y1="0" x2="1" y2="0">
          <stop offset="0" stop-color="var(--navy-soft)"/>
          <stop offset="0.55" stop-color="var(--navy)"/>
          <stop offset="1" stop-color="var(--navy-deep)"/>
        </linearGradient>
        <linearGradient id="orangeBand" x1="0" y1="0" x2="1" y2="1">
          <stop offset="0" stop-color="var(--orange)"/>
          <stop offset="1" stop-color="var(--orange-deep)"/>
        </linearGradient>
        <linearGradient id="frostPanel" x1="0" y1="0" x2="1" y2="1">
          <stop offset="0" stop-color="var(--frost-mid)"/>
          <stop offset="0.45" stop-color="var(--frost-light)"/>
          <stop offset="1" stop-color="var(--frost-mid)"/>
        </linearGradient>
      </defs>
      <rect class="navy-field" width="1050" height="596" fill="url(#navyField)"/>
      <rect class="orange-band" x="830" width="220" height="596" fill="url(#orangeBand)"/>
      <polygon class="hex-panel" points="487,298 620,0 840,0 967,298 840,596 620,596" fill="url(#frostPanel)"/>
    </svg>

    <div class="contact-block">
      <p class="person-name">Lena Marsh</p>
      <p class="person-role">Project Manager</p>
      <p class="licence">Lic No.,482916c</p>
      <ul class="contact-list">
        <li>
          <svg class="contact-icon" viewBox="0 0 24 24" aria-hidden="true">
            <rect x="6" y="1" width="12" height="22" rx="2" fill="none" stroke="var(--orange)" stroke-width="2.4"/>
            <circle cx="12" cy="19" r="1.4" fill="var(--orange)"/>
          </svg>
          0400 555 017
        </li>
        <li>
          <svg class="contact-icon" viewBox="0 0 24 24" aria-hidden="true">
            <rect x="1" y="5" width="22" height="14" fill="var(--orange)"/>
            <path d="M1 5 L12 13 L23 5" fill="none" stroke="var(--navy)" stroke-width="1.8"/>
          </svg>
          hello@setwelltiling.com.au
        </li>
        <li>
          <svg class="contact-icon" viewBox="0 0 24 24" aria-hidden="true">
            <circle cx="12" cy="12" r="10" fill="var(--orange)"/>
            <ellipse cx="12" cy="12" rx="4" ry="10" fill="none" stroke="var(--navy)" stroke-width="1.5"/>
            <line x1="2" y1="12" x2="22" y2="12" stroke="var(--navy)" stroke-width="1.5"/>
          </svg>
          www.setwelltiling.com.au
        </li>
      </ul>
    </div>

    <p class="brand-name">SETWELL TILING</p>
  </div>
</body>
</html>
```